Flyer Design Project

I need a cool design that describes a new line of services I am selling. The final product should be a 8 1/2 by 11 and maximum two pages.

I am selling consulting services to learn to use web conferencing tools for business development, meeting and training.
Updates

Please use the file I have attached as a guide for your work. It is a document called "guide-quickofficehints" and I love its design.

Thanks

                                        Please substitute the new text availble and just uploaded in the FLYER. Please submit the FINAL version fo your design with TExt changes as well as improvements detailed in previous message. 

Target Market(s)

Entrepreneurs and classroom educators who wnats to explore a new way to teach (innovators not scared of technology)

Industry/Entity Type

Business

Requirements
Must have
• I would like to receive a final PDF with the content EDITABLE for minor edits (I have acrobat)
Logo should be included (attached)

PLEASE CHECK OUT ATTACHED DOCUMENT WHOSE DESIGN I LOVE.
IT is called "Guide quick-office hints". If you could follow that as a template to design mine that would be great!

```html
<!DOCTYPE html>
<html lang="en">
<head>
<meta charset="utf-8">
<title>Convene Consulting – Online Meeting Skills Services</title>
<link rel="stylesheet" href="https://fonts.googleapis.com/css2?family=Mulish:ital,wght@0,400;0,600;0,700;0,800;1,400&display=swap">
<style>
  :root {
    --orange: #d9661f;
    --ink: #2b2420;
    --grey: #4a4a4a;
    --white: #ffffff;
    --backdrop: #e6e3df;
    --photo-light: #f6efe9;
    --photo-warm: #c98a62;
    --photo-deep: #8e5637;
  }
  * { box-sizing: border-box; margin: 0; padding: 0; }
  html, body { width: 1200px; height: 900px; overflow: hidden; }
  body {
    background: var(--backdrop);
    font-family: "Mulish", Arial, sans-serif;
    color: var(--ink);
    position: relative;
  }
  .page {
    position: absolute;
    top: 88px;
    width: 560px;
    height: 725px;
    box-shadow: 0 4px 14px rgba(0,0,0,0.18);
    overflow: hidden;
  }

  /* Cover */
  .cover { left: 25px; background: var(--white); }
  .brand { display: flex; flex-direction: column; align-items: flex-end; }
  .brand-name {
    font-weight: 800;
    font-size: 25px;
    letter-spacing: 0.5px;
    color: var(--grey);
    line-height: 1;
  }
  .brand-tagline {
    font-size: 10.5px;
    color: var(--orange);
    margin-top: 5px;
    letter-spacing: 0.3px;
  }
  .cover .brand { position: absolute; top: 40px; right: 36px; }
  .cover-photo {
    position: absolute;
    top: 110px;
    left: 0;
    width: 100%;
    height: 330px;
    background: radial-gradient(ellipse at 55% 55%, var(--photo-warm) 0%, var(--photo-deep) 38%, #d9b59c 62%, var(--photo-light) 85%);
  }
  .cover-title {
    position: absolute;
    top: 460px;
    left: 215px;
    width: 320px;
    padding-left: 14px;
    border-left: 6px solid var(--orange);
  }
  .cover-title h1 {
    font-weight: 800;
    font-size: 34px;
    line-height: 1.12;
    color: var(--orange);
  }
  .cover-title p {
    font-size: 34px;
    color: var(--grey);
    margin-top: 4px;
    line-height: 1.15;
  }

  /* Services page */
  .services { left: 615px; background: var(--orange); color: var(--ink); }
  .services-header {
    background: var(--white);
    height: 62px;
    display: flex;
    align-items: center;
    justify-content: space-between;
    padding: 0 26px;
  }
  .services-header .brand { align-items: flex-start; }
  .services-header .brand-name { font-size: 16px; }
  .services-header .brand-tagline { font-size: 7px; margin-top: 3px; }
  .services-header h2 {
    font-weight: 800;
    font-size: 13px;
    color: var(--orange);
    letter-spacing: 0.4px;
  }
  .services-body { padding: 16px 30px 0; font-size: 9.2px; line-height: 1.42; }
  .services-body h3 {
    color: var(--white);
    font-weight: 800;
    font-size: 12px;
    line-height: 1.3;
    margin: 14px 0 4px;
  }
  .services-body h3:first-child { margin-top: 0; }
  .lead { font-style: italic; margin-bottom: 6px; }
  .services-body p { margin-bottom: 6px; }
  .points { list-style: none; margin: 0 0 4px; }
  .points li { position: relative; padding-left: 10px; margin-bottom: 3px; }
  .points li::before { content: "•"; position: absolute; left: 0; color: var(--white); }
  .offer { margin-bottom: 8px; }
  .offer-name { font-weight: 800; color: var(--white); display: block; margin-bottom: 2px; }
  .offer-text { padding-left: 10px; display: block; }
  .contact {
    position: absolute;
    bottom: 20px;
    left: 30px;
    right: 30px;
    border-top: 1px solid rgba(255,255,255,0.6);
    padding-top: 9px;
    text-align: center;
    font-weight: 800;
    font-size: 11px;
    color: var(--white);
  }
</style>
</head>
<body>

<section class="page cover">
  <div class="brand">
    <span class="brand-name">Convene Consulting</span>
    <span class="brand-tagline">Learn. Connect. Grow.</span>
  </div>
  <div class="cover-photo" role="img" aria-label="Photograph of a ceramic piggy bank in warm orange light"></div>
  <div class="cover-title">
    <h1>Online Meeting Skills Services:</h1>
    <p>It is just the beginning…</p>
  </div>
</section>

<section class="page services">
  <header class="services-header">
    <div class="brand">
      <span class="brand-name">Convene Consulting</span>
      <span class="brand-tagline">Learn. Connect. Grow.</span>
    </div>
    <h2>ONLINE MEETING SKILLS SERVICES</h2>
  </header>

  <div class="services-body">
    <h3>What if your business can reach all the people already interested in learning what you know?</h3>
    <p class="lead">A different use of webinar technology: the first step towards a new way of thinking about your marketing and clients.</p>
    <p>You probably know about webinars. You may have attended a few yourself and found them dull or one-sided. It does not have to be that way. A well-run online session can teach, persuade and build trust with the people who already want what you offer. We help you turn your expertise into lively, interactive online sessions that people remember and share.</p>
    <ul class="points">
      <li>We design an effective virtual meeting experience using the tools of the online room to their full potential and the habits of good facilitation.</li>
      <li>We repurpose your marketing materials for engaging online sessions and help you build a simple plan to invite your existing list.</li>
      <li>We support you live as you deliver your first session, so every detail is rehearsed and you are ready on the day.</li>
    </ul>

    <h3>Choose the service that best fit your needs and budget. A new level of online engagement and virtual collaboration awaits.</h3>
    <div class="offer">
      <span class="offer-name">• Webinar Essentials: Outfitting the Online Entrepreneur</span>
      <span class="offer-text">Three hours of one-on-one online coaching that gives you all you need to know about web conferencing tools and online meeting practice. Includes access to our online resource library. ($400)</span>
    </div>
    <div class="offer">
      <span class="offer-name">• Fast-track CFW: Webinar Facilitator Certification in 2 weeks</span>
      <span class="offer-text">Seven hours of one-on-one online coaching to learn about web conferencing tools and how to use them for your training sessions. Includes our Webinar Facilitator Certification and your own meeting room for one month ($1,000).</span>
    </div>
    <div class="offer">
      <span class="offer-name">• “Turnkey” Solution: Your 60-minute Webinar</span>
      <span class="offer-text">Plan, design, develop and deliver one webinar session on the content of your expertise, marketed to your audience. We set it up, handle the registration process and coach you on the delivery with four hours of one-on-one coaching. Includes your own meeting room for one month ($1,800).</span>
    </div>

    <h3>You’ll participate via the MeetSpace Live Meeting platform. No special software is required, if you have a computer with Internet</h3>
    <p>As a professional communicator, whether you are a small business owner, an educator or a manager, you know that webinar technology is here to stay. Have you wondered how to use them to benefit your business? Leave the details to us. Well-implemented online sessions can give your business unparalleled access to new markets at a minimum cost.</p>
  </div>

  <footer class="contact">Want to know more? Call us at 202-555-0147 or email us at hello@conveneconsult.com</footer>
</section>

</body>
</html>
```